High-end Oceanfront Real Estate Group Needs Clean, Modern Web Design

I’m looking for a clean, professional, modern and beautiful homepage web design for a Real Estate group in Southern California, USA.

The group/company is “Marwick on the Shore,” and they specialize in high end (i.e. expensive), oceanfront real estate in the Orange County area.

The look and feel of the page should accentuate the brand qualities: luxurious/expensive, professional, and beautiful (Orange County is one of the most beautiful areas in all the US and we would love the site to emphasize the beautiful beaches and scenery it has to offer).

Looks we like:
• www.brantleyhomesrealty.example
• www.closedbyvane.example -- I think the design is pretty out-dated in this site, but I like the organization/layout of the site

Header Tags (I don’t know if we can fit all of these, may need a side-menu, but I’d prefer header title only if possible):
• Welcome
• Featured Listings
• Previously Sold
• Sell
• Property Search
• Team
• Videos
• Blog
• Explore O.C.
• Contact

I have attached the beach and logo pics that we would like to use as the header, a few pictures of the team, and one sample home/view pic which can be used in any of the other sections (for pictures of the homes, just find expensive oceanfront houses and that will be fine).

I promise to provide feedback to each and every design submission. I appreciate the hard work that all of you are putting into your designs. There can be only one contest winner, but I hope to give all of you helpful feedback to submit the best designs possible!

Target Market(s)

Very wealthy home owners of oceanfront properties. These properties are worth several millions of dollars, and thus the site and brand needs to be targeted to very wealthy, successful individuals and families (both US and international buyers).

Industry/Entity Type

Real Estate

Number of Pages Required

2 page

Requirements
Must have
• I don’t want to give too many requirements, because I want to let you all be creative. However, here are the few Must Haves:
• Must submit 2 page designs (a home page and a sub page)
• Must use logo provided
• Focus is mostly on homes, but I would like to include some beach/ocean imagery as well
• The first “item” on the home page should be an accordion/slider which shows pictures of homes and with 1 line of text: “List with the Leader” and two link buttons: “Sell Your Home” and “Buy Your Home”
• Color palette needs to be mainly blues--to match ocean and sky blue
• Exported in all major formats (psd,ai,eps,png,jpeg,etc)
Nice to have
• We don’t necessarily need all of these, but would like to feature most:
• List of videos
• “Meet the Team”—brief team bios and pics
• Link(s) to Blog
• “List with the Leader” – section on why they should choose this firm
• Featured Listings
• Previously Sold

```html
<!DOCTYPE html>
<html lang="en">
<head>
<meta charset="utf-8">
<title>Marwick on the Shore — Oceanfront Real Estate</title>
<link rel="stylesheet" href="https://fonts.googleapis.com/css2?family=Source+Sans+Pro:ital,wght@0,300;0,400;0,600;0,700;1,400&family=Roboto+Condensed:wght@700&display=swap">
<style>
:root{
  --blue:#1ba1cf;
  --blue-dark:#1487b3;
  --ink:#3d3d3d;
  --muted:#7a7a7a;
  --rule:#cfcfcf;
  --light:#f6f6f6;
  --white:#ffffff;
  --sans:"Source Sans Pro", Arial, sans-serif;
  --cond:"Roboto Condensed", Arial Narrow, sans-serif;
}
*{box-sizing:border-box;margin:0;padding:0}
html,body{width:1200px;height:3509px;overflow:hidden}
body{font-family:var(--sans);color:var(--ink);background:var(--white)}
section,header,footer{position:relative;width:1200px;overflow:hidden}
.photo{position:absolute;inset:0}
.abs{position:absolute;left:0;right:0;text-align:center}
.section-title{font-weight:300;font-size:27px;letter-spacing:.5px;text-transform:uppercase}
.rule{position:absolute;left:560px;width:80px;height:2px;background:var(--rule)}
.rule.light{background:rgba(255,255,255,.85)}
.btn-outline{display:inline-block;border:1.5px solid currentColor;font-family:var(--cond);font-size:11px;letter-spacing:1px;text-transform:uppercase;text-align:center}
.btn-solid{display:inline-block;background:var(--blue);color:var(--white);font-family:var(--cond);font-size:13px;letter-spacing:1.5px;text-transform:uppercase;text-align:center}

/* Hero */
.hero{height:451px;color:var(--white)}
.hero .photo{background:linear-gradient(180deg,#2c3a24 0%,#4d5a3c 35%,#8a8a78 60%,#6a6f62 80%,#3b4436 100%)}
.hero .photo::after{content:"";position:absolute;inset:0;background:rgba(0,0,0,.18)}
.brand{top:30px;font-weight:300;font-size:40px;letter-spacing:4px;text-transform:uppercase}
.main-nav{top:146px;display:flex;justify-content:center;gap:22px;font-size:11px;font-weight:600;letter-spacing:.3px;text-transform:uppercase}
.hero-title{top:206px;font-weight:300;font-size:48px;letter-spacing:2px}
.hero .rule{top:278px}
.hero-actions{top:316px;display:flex;justify-content:center;gap:22px}
.hero-actions span{width:140px;height:34px;line-height:34px}
.hero-actions .btn-outline{color:var(--white);font-size:12px}
.dots{top:396px;display:flex;justify-content:center;gap:6px}
.dots i{width:10px;height:10px;border-radius:50%;background:var(--white)}
.dots i.on{background:var(--blue)}

/* About */
.about{height:321px;color:var(--white)}
.about .photo{background:linear-gradient(135deg,#1e9fd0 0%,#2aa8d6 40%,#1993c4 70%,#2aa6d3 100%)}
.about .section-title{top:54px}
.about .rule{top:102px}
.about-cols{position:absolute;top:145px;left:199px;width:800px;display:flex;justify-content:space-between}
.about-col{width:232px}
.about-col h3{font-weight:300;font-size:18px;margin-bottom:8px}
.about-col p{font-size:11px;line-height:14px;margin-bottom:18px}
.about-col .btn-outline{width:94px;height:28px;line-height:26px;font-size:10px}

/* Listings */
.listings{height:531px;background:var(--light)}
.tabs{top:44px;display:flex;justify-content:center;gap:32px;font-weight:300;font-size:27px;text-transform:uppercase}
.tabs span{padding-bottom:6px;border-bottom:2px solid var(--ink);color:#555}
.tabs span.active{color:var(--blue);border-color:var(--blue)}
.cards{position:absolute;top:136px;left:199px;width:800px;display:flex;justify-content:space-between}
.card{width:234px;height:273px;background:var(--white);box-shadow:0 1px 3px rgba(0,0,0,.08);text-align:center}
.card .thumb{position:relative;height:147px;background:linear-gradient(180deg,#9fc4e2 0%,#c9d8e2 35%,#a58d73 55%,#7e8aa0 100%)}
.card h3{margin-top:20px;color:var(--blue);font-weight:400;font-size:15px;text-transform:uppercase;letter-spacing:.5px}
.card p{margin:8px auto 0;width:170px;font-style:italic;font-size:10px;line-height:13px;color:var(--muted)}
.card svg{margin-top:14px}
.listings .more{top:458px}
.listings .btn-outline{width:130px;height:32px;line-height:30px;color:#555;border-color:#999}

/* Sell */
.sell{height:383px;color:var(--white)}
.sell .photo{background:linear-gradient(180deg,#3f6f95 0%,#7fa7c5 30%,#b9cad4 48%,#9a8a72 68%,#6f5f4d 100%)}
.sell .photo::after{content:"";position:absolute;inset:0;background:rgba(10,25,45,.35)}
.sell .section-title{top:54px}
.sell .rule{top:102px}
.sell-copy{position:absolute;top:142px;left:199px;width:802px;text-align:center;font-size:11.5px;line-height:17px}
.sell .more{top:301px}
.sell .btn-outline{width:130px;height:32px;line-height:30px;color:var(--white)}

/* Videos */
.videos{height:524px}
.videos .section-title{top:54px;color:#555}
.videos .rule{top:104px}
.video-grid{position:absolute;top:162px;left:199px;width:800px;height:296px;display:grid;grid-template-columns:402px 199px 199px;grid-template-rows:148px 148px}
.video{position:relative}
.video.feature{grid-row:1 / span 2;background:linear-gradient(135deg,#6f6a5e 0%,#b9a88c 45%,#4a3d33 100%)}
.video.street{background:linear-gradient(180deg,#9bb0c2 0%,#8f8777 55%,#5b5d60 100%)}
.video .play{position:absolute;left:50%;top:50%;transform:translate(-50%,-50%)}

/* Team */
.team{height:475px;background:var(--light)}
.team .section-title{top:54px;color:#555}
.team .rule{top:104px}
.team-cards{position:absolute;top:152px;left:199px;width:800px;display:flex;justify-content:space-between}
.member{display:flex;width:390px;height:262px;background:var(--white);box-shadow:0 1px 3px rgba(0,0,0,.08)}
.member .portrait{width:175px;height:262px}
.member .portrait.one{background:linear-gradient(180deg,#4a3a2e 0%,#7a6452 50%,#5a4f47 100%)}
.member .portrait.two{background:linear-gradient(180deg,#b8a48c 0%,#e3cdb1 50%,#cdb39a 100%)}
.member .bio{flex:1;padding:24px 18px 0;text-align:center}
.member h3{color:var(--blue);font-weight:400;font-size:15px;text-transform:uppercase;letter-spacing:.5px}
.member p{margin:8px 0 16px;font-style:italic;font-size:10px;line-height:13px;color:var(--muted)}
.member .btn-solid{width:145px;height:32px;line-height:32px}

/* Testimonials */
.testimonials{height:419px;color:var(--white)}
.testimonials .photo{background:linear-gradient(180deg,#3c3f45 0%,#6a5a4a 35%,#c58a45 55%,#5a4a3c 75%,#2c3a48 100%)}
.testimonials .photo::after{content:"";position:absolute;inset:0;background:rgba(0,0,0,.25)}
.testimonials .section-title{top:56px}
.avatar{position:absolute;top:156px;left:552px;width:96px;height:96px;border-radius:50%;border:4px solid var(--white);background:linear-gradient(180deg,#8a6a50,#c9a184)}
.client-name{top:268px;color:var(--blue);font-size:15px;text-transform:uppercase}
.client-co{top:290px;font-size:10px;text-transform:uppercase;letter-spacing:.3px}
.quote{position:absolute;top:316px;left:310px;width:580px;text-align:center;font-size:11.5px;line-height:16px}
.arrow{position:absolute;top:238px}
.arrow.prev{left:208px}
.arrow.next{left:964px}

/* Subscribe */
.subscribe{height:182px;background:var(--blue);color:var(--white)}
.subscribe .section-title{top:28px}
.subscribe .rule{top:76px}
.sub-form{position:absolute;top:110px;left:433px;width:334px;height:37px;display:flex}
.sub-form .field{flex:1;background:var(--white);color:#aaa;font-size:9px;text-transform:uppercase;letter-spacing:.5px;line-height:37px;padding-left:14px}
.sub-form .send{width:89px;background:#c8c8c8;color:var(--white);font-size:10px;text-transform:uppercase;text-align:center;line-height:37px}

/* Partners */
.partners{height:99px;border-bottom:1px solid #e3e3e3}
.partners svg{position:absolute;left:0;top:0}

/* Footer */
.site-footer{height:124px}
.social{top:18px;display:flex;justify-content:center;gap:6px}
.social i{width:24px;height:24px;border-radius:50%;background:#555}
.foot-nav{top:64px;display:flex;justify-content:center;gap:14px;font-size:10px;color:#666}
.copyright{top:82px;font-size:10px;color:#777}
.copyright b{font-weight:400;color:var(--blue)}
</style>
</head>
<body>

<header class="hero">
  <div class="photo" role="img" aria-label="Photo of a luxury oceanfront estate with palm trees, a stone terrace and garden stairs"></div>
  <div class="abs brand">Marwick on the Shore</div>
  <nav class="abs main-nav">
    <span>Home</span><span>Featured Listing</span><span>Previously Sold</span><span>Sell</span><span>Property Search</span><span>Team</span><span>Videos</span><span>Blog</span><span>Explore O.C.</span><span>Contact</span>
  </nav>
  <h1 class="abs hero-title">LIST WITH THE LEADER</h1>
  <div class="rule light" style="top:278px"></div>
  <div class="abs hero-actions">
    <span class="btn-outline">Sell Your Home</span>
    <span class="btn-solid">Buy Your Home</span>
  </div>
  <div class="abs dots"><i></i><i class="on"></i><i></i></div>
</header>

<section class="about">
  <div class="photo" role="img" aria-label="Soft blue background band"></div>
  <h2 class="abs section-title">About Who We Are</h2>
  <div class="rule light" style="top:102px"></div>
  <div class="about-cols">
    <div class="about-col">
      <h3>About Company</h3>
      <p>Lorem ipsum dolor sit amet, consectetur adipiscing elit. Integer placerat dolor varius semper elementum. Nullam quis arcu eget dolor sollicitudin ornare.</p>
      <span class="btn-outline">Learn More</span>
    </div>
    <div class="about-col">
      <h3>About Properties</h3>
      <p>Lorem ipsum dolor sit amet, consectetur adipiscing elit. Integer placerat dolor varius semper elementum. Nullam quis arcu eget dolor sollicitudin ornare.</p>
      <span class="btn-outline">Learn More</span>
    </div>
    <div class="about-col">
      <h3>Why Choose Us</h3>
      <p>Lorem ipsum dolor sit amet, consectetur adipiscing elit. Integer placerat dolor varius semper elementum. Nullam quis arcu eget dolor sollicitudin ornare.</p>
      <span class="btn-outline">Learn More</span>
    </div>
  </div>
</section>

<section class="listings">
  <div class="abs tabs"><span class="active">Featured Listings</span><span>Previously Sold</span></div>
  <div class="cards">
    <article class="card">
      <div class="thumb" role="img" aria-label="Photo of a residential street with townhouses and parked cars"></div>
      <h3>Project Name</h3>
      <p>Lorem ipsum dolor sit amet, consectetur adipiscing elit. Proin sagittis.</p>
      <svg width="36" height="10" viewBox="0 0 36 10"><path d="M0 5H34M29 1L34 5L29 9" fill="none" stroke="#1ba1cf" stroke-width="1.5"/></svg>
    </article>
    <article class="card">
      <div class="thumb" role="img" aria-label="Photo of a residential street with townhouses and parked cars"></div>
      <h3>Project Name</h3>
      <p>Lorem ipsum dolor sit amet, consectetur adipiscing elit. Proin sagittis.</p>
      <svg width="36" height="10" viewBox="0 0 36 10"><path d="M0 5H34M29 1L34 5L29 9" fill="none" stroke="#1ba1cf" stroke-width="1.5"/></svg>
    </article>
    <article class="card">
      <div class="thumb" role="img" aria-label="Photo of a residential street with townhouses and parked cars"></div>
      <h3>Project Name</h3>
      <p>Lorem ipsum dolor sit amet, consectetur adipiscing elit. Proin sagittis.</p>
      <svg width="36" height="10" viewBox="0 0 36 10"><path d="M0 5H34M29 1L34 5L29 9" fill="none" stroke="#1ba1cf" stroke-width="1.5"/></svg>
    </article>
  </div>
  <div class="abs more"><span class="btn-outline">See More Listings</span></div>
</section>

<section class="sell">
  <div class="photo" role="img" aria-label="Photo of a beach with a parasol and deck chairs under a cloudy sky"></div>
  <h2 class="abs section-title">Sell</h2>
  <div class="rule light" style="top:102px"></div>
  <p class="sell-copy">Lorem ipsum dolor sit amet, consectetur adipiscing elit. In pharetra vehicula nulla id eleifend. Donec sagittis vitae turpis a finibus. Aenean dapibus vestibulum elit sed euismod. Aliquam sit amet laoreet ante. Aenean porta lacus sit amet sagittis vehicula. Suspendisse suscipit orci et enim efficitur, eu tempus ligula congue. Sed at sodales nulla. In velit lorem, mattis et blandit at, faucibus eu enim. Pellentesque finibus in neque ut tincidunt. Pellentesque ut dolor vehicula, congue tellus eu, varius metus. Praesent nulla ipsum, accumsan sed pulvinar eu, rutrum ac ante. Nunc pharetra arcu eu nisi tincidunt, ut pretium libero convallis. Etiam quis nibh bibendum libero accumsan condimentum. Duis et enim sit amet neque congue consequat. Morbi nec purus sed diam ornare facilisis at eget leo. Proin consectetur tincidunt odio vehicula tempus. Mauris non elementum justo.</p>
  <div class="abs more"><span class="btn-outline">Learn More</span></div>
</section>

<section class="videos">
  <h2 class="abs section-title">Featured Videos</h2>
  <div class="rule" style="top:104px"></div>
  <div class="video-grid">
    <div class="video feature" role="img" aria-label="Video still of a couple on a covered patio overlooking trees">
      <svg class="play" width="40" height="30" viewBox="0 0 40 30"><rect width="40" height="30" rx="6" fill="#111"/><path d="M16 9L26 15L16 21Z" fill="#fff"/></svg>
    </div>
    <div class="video street" role="img" aria-label="Video still of a townhouse street">
      <svg class="play" width="30" height="22" viewBox="0 0 40 30"><rect width="40" height="30" rx="6" fill="#111"/><path d="M16 9L26 15L16 21Z" fill="#fff"/></svg>
    </div>
    <div class="video street" role="img" aria-label="Video still of townhouse facades">
      <svg class="play" width="30" height="22" viewBox="0 0 40 30"><rect width="40" height="30" rx="6" fill="#111"/><path d="M16 9L26 15L16 21Z" fill="#fff"/></svg>
    </div>
    <div class="video street" role="img" aria-label="Video still of townhouses along a road">
      <svg class="play" width="30" height="22" viewBox="0 0 40 30"><rect width="40" height="30" rx="6" fill="#111"/><path d="M16 9L26 15L16 21Z" fill="#fff"/></svg>
    </div>
    <div class="video street" role="img" aria-label="Video still of a modern apartment building">
      <svg class="play" width="30" height="22" viewBox="0 0 40 30"><rect width="40" height="30" rx="6" fill="#111"/><path d="M16 9L26 15L16 21Z" fill="#fff"/></svg>
    </div>
  </div>
</section>

<section class="team">
  <h2 class="abs section-title">Meet the Team</h2>
  <div class="rule" style="top:104px"></div>
  <div class="team-cards">
    <article class="member">
      <div class="portrait one" role="img" aria-label="Portrait of team member Glen in a suit"></div>
      <div class="bio">
        <h3>Glen</h3>
        <p>Lorem ipsum dolor sit amet, consectetur adipiscing elit. In pharetra vehicula nulla id eleifend. Donec sagittis vitae turpis a finibus. Aenean dapibus vestibulum elit sed euismod. Aliquam sit amet laoreet ante. Aenean porta lacus sit amet sagittis vehicula. Suspendisse suscipit orci et enim efficitur, eu tempus ligula congue.</p>
        <span class="btn-solid">Read More</span>
      </div>
    </article>
    <article class="member">
      <div class="portrait two" role="img" aria-label="Portrait of team member Nora Marwick"></div>
      <div class="bio">
        <h3>Nora Marwick</h3>
        <p>Lorem ipsum dolor sit amet, consectetur adipiscing elit. In pharetra vehicula nulla id eleifend. Donec sagittis vitae turpis a finibus. Aenean dapibus vestibulum elit sed euismod. Aliquam sit amet laoreet ante. Aenean porta lacus sit amet sagittis vehicula. Suspendisse suscipit orci et enim efficitur, eu tempus ligula congue.</p>
        <span class="btn-solid">Read More</span>
      </div>
    </article>
  </div>
</section>

<section class="testimonials">
  <div class="photo" role="img" aria-label="Photo of a sunset over the ocean shoreline"></div>
  <h2 class="abs section-title">What Our Client Speak About Us</h2>
  <div class="avatar" role="img" aria-label="Client portrait"></div>
  <div class="abs client-name">Evan Hale</div>
  <div class="abs client-co">A Lorem Ipsum Co.</div>
  <p class="quote">Ut id erat quis magna faucibus molestie non vel ligula. Etiam non viverra tortor, sit amet ullamcorper dolor. Sed suscipit consectetur nulla laoreet suscipit. Duis et erat non lacus sagittis pharetra sed in orci. In hac habitasse platea dictumst. Aenean sagittis.</p>
  <svg class="arrow prev" width="28" height="40" viewBox="0 0 28 40"><path d="M22 4L6 20L22 36" fill="none" stroke="#fff" stroke-width="3"/></svg>
  <svg class="arrow next" width="28" height="40" viewBox="0 0 28 40"><path d="M6 4L22 20L6 36" fill="none" stroke="#fff" stroke-width="3"/></svg>
</section>

<section class="subscribe">
  <h2 class="abs section-title">Subscribe to Our Newletter</h2>
  <div class="rule light" style="top:76px"></div>
  <div class="sub-form"><span class="field">Enter your email id</span><span class="send">Subscribe</span></div>
</section>

<section class="partners" aria-label="Partner associations">
  <svg width="1200" height="99" viewBox="0 0 1200 99">
    <rect x="356" y="34" width="52" height="30" rx="3" fill="#e9b64a"/>
    <rect x="456" y="34" width="58" height="30" rx="3" fill="#3b7fbf"/>
    <circle cx="596" cy="49" r="17" fill="#d8262e"/>
    <circle cx="716" cy="49" r="18" fill="#5a6f8a"/>
    <circle cx="816" cy="49" r="19" fill="#6fb843"/>
  </svg>
</section>

<footer class="site-footer">
  <div class="abs social"><i></i><i></i><i></i></div>
  <nav class="abs foot-nav">
    <span>Home</span><span>Featured Listing</span><span>Previously Sold</span><span>Sell</span><span>Property Search</span><span>Team</span><span>Videos</span><span>Blog</span><span>Explore O.C.</span><span>Contact</span>
  </nav>
  <div class="abs copyright">Copyright © 2016 <b>Marwick on the Shore</b>. All Rights Reserved.</div>
</footer>

</body>
</html>
```